Meridale Nutrition needs Stationary and a business card

We would like to use our current logo. The text can be moved around as needed. The stationary needs to be a 'first page' where the logo is more prominent to be impressive on higher quality paper and a second page where the logo is more subtle where there will be much more information on the page. There are 2 clinic locations which will need include name, address, phone number, fax number, web address. The business card should be single sided and contain this information also.
The design must be contemporary and sophisticated as this is a science based diet run out of a medical clinic.

Target Market(s)

People wanting to lose weight, athletes looking to optimise performance, people with arthritis or fighting cancer

Industry/Entity Type

Business

Contact Information for Business Card

must use the logo. I have attached an example card with the practice details on it. there must be space for the doctors name. Also the website www.meridalenutrition.com.au

Requirements
Must have
• the logo, the business adresses and phone numbers, the website, the doctors name and qualifications
Nice to have
• some creativity
Should not have
• Do not simply reproduce the existing card please

```html
<!DOCTYPE html>
<html lang="en">
<head>
<meta charset="utf-8">
<title>Meridale Nutrition – Stationery</title>
<link href="https://fonts.googleapis.com/css2?family=Questrial&display=swap" rel="stylesheet">
<style>
  :root {
    --backdrop: #e6e7e9;
    --paper: #ffffff;
    --brand-navy: #336799;
    --brand-sky: #3bc3f0;
    --watermark-ring: #e6eaf3;
    --watermark-fill: #eef5fc;
    --cover-ring: #7f9cc7;
    --cover-fill: #3a89bc;
    --ink-light: #ffffff;
  }
  * { margin: 0; padding: 0; box-sizing: border-box; }
  html, body {
    width: 1200px; height: 790px; overflow: hidden;
    background: var(--backdrop);
    font-family: "Questrial", sans-serif;
  }
  .canvas { position: relative; width: 1200px; height: 790px; }

  .sheet {
    position: absolute; top: 67px; width: 504px; height: 651px;
    overflow: hidden;
    box-shadow: 3px 4px 6px rgba(0,0,0,0.35);
  }
  .sheet--letterhead { left: 65px; background: var(--paper); }
  .sheet--cover { left: 610px; background: var(--brand-navy); }

  /* letterhead header */
  .header-brand {
    position: absolute; left: 21px; top: 16px;
    display: flex; align-items: center; gap: 14px;
  }
  .brand-dot {
    width: 58px; height: 58px; border-radius: 50%;
    background: var(--brand-sky); border: 4px solid var(--brand-navy);
  }
  .brand-name {
    color: var(--brand-navy); font-size: 17px; letter-spacing: 0.6px;
    text-transform: uppercase;
    border-bottom: 2px solid var(--brand-sky); padding-bottom: 3px;
  }

  .watermark { position: absolute; border-radius: 50%; }
  .watermark--letterhead {
    left: 151px; top: 279px; width: 200px; height: 200px;
    border: 6px solid var(--watermark-ring);
    background: var(--watermark-fill);
  }
  .watermark--cover {
    left: 136px; top: 211px; width: 232px; height: 232px;
    border: 6px solid var(--cover-ring);
    background: var(--cover-fill);
  }

  /* letterhead footer band */
  .contact-band {
    position: absolute; left: 0; bottom: 0; width: 100%; height: 81px;
    background: var(--brand-navy); color: var(--ink-light);
  }
  .clinic {
    position: absolute; top: 8px; width: 180px;
    font-size: 10.5px; line-height: 12px;
  }
  .clinic--left { left: 20px; }
  .clinic--right { left: 219px; }
  .clinic .row { position: relative; }
  .clinic .phone { position: absolute; top: 0; white-space: nowrap; }
  .clinic--left .phone { left: 104px; }
  .clinic--right .phone { left: 102px; }
  .clinic .service { margin-top: 5px; }
  .clinic .web { font-size: 11.5px; margin-top: 3px; white-space: nowrap; }
  .band-divider {
    position: absolute; left: 207px; top: 10px; width: 1px; height: 62px;
    background: var(--ink-light);
  }

  .corner-mark {
    position: absolute; left: 408px; top: 561px;
    width: 96px; height: 96px; border-radius: 50%;
    background: var(--brand-sky);
    border: 5px solid var(--brand-navy);
    box-shadow: 0 0 0 6px var(--paper);
  }
  .sheet--cover .corner-mark { left: 407px; box-shadow: none; border-width: 6px; }

  /* cover footer */
  .cover-band {
    position: absolute; left: 0; bottom: 0; width: 100%; height: 81px;
    background: var(--paper);
  }
  .cover-name {
    position: absolute; left: 28px; top: 12px; width: 360px;
    text-align: center; white-space: nowrap;
    color: var(--brand-navy); font-size: 28px; letter-spacing: 0.5px;
    text-transform: uppercase;
    border-bottom: 3px solid var(--brand-sky); padding-bottom: 5px;
  }
</style>
</head>
<body>
<main class="canvas">

  <section class="sheet sheet--letterhead">
    <header class="header-brand">
      <div class="brand-dot"></div>
      <div class="brand-name">Meridale Nutrition</div>
    </header>

    <div class="watermark watermark--letterhead" role="img" aria-label="Faint circular brand emblem"></div>

    <footer class="contact-band">
      <div class="clinic clinic--left">
        <div>Kellerton</div>
        <div>52-54 Harlow Road</div>
        <div class="row"><span>Kellerton NSW 2190</span><span class="phone">T: 02 9000 4812</span></div>
        <div class="service">Shoulder and Elbow</div>
        <div class="web">www.meridalenutrition.com.au</div>
      </div>
      <div class="band-divider"></div>
      <div class="clinic clinic--right">
        <div>Brayfield</div>
        <div>118 Linden Road</div>
        <div class="row"><span>Brayfield NSW 2045</span><span class="phone">F: 02 9000 7365</span></div>
        <div class="service">Knee Surgery</div>
        <div class="web">www.meridalenutrition.com.au</div>
      </div>
    </footer>
    <div class="corner-mark"></div>
  </section>

  <section class="sheet sheet--cover">
    <div class="watermark watermark--cover" role="img" aria-label="Large tinted circular brand emblem"></div>
    <footer class="cover-band">
      <div class="cover-name">Meridale Nutrition</div>
    </footer>
    <div class="corner-mark"></div>
  </section>

</main>
</body>
</html>
```